VOMRA Pty Ltd Business Card

Looking for a simple yet eye-catching double-sided business card design using my company logo on one side and contact details on the other.

Target Market(s)

Government

Industry/Entity Type

Communication Systems Engineering

Contact Information for Business Card

VOMRA Pty Ltd

Requirements
Nice to have
• Would be great to have a QR code so details can be scanned into contacts

```html
<!DOCTYPE html>
<html lang="en">
<head>
<meta charset="utf-8">
<title>VOMRA Pty Ltd Business Card</title>
<link rel="stylesheet" href="https://fonts.googleapis.com/css2?family=Open+Sans:wght@400;600;700&display=swap">
<style>
  :root {
    --page-bg: #e9e6e2;
    --card-light: #ffffff;
    --card-dark: #343f47;
    --ink: #2e3a42;
    --ink-soft: #3d474e;
    --emboss: #2a343b;
    --divider: #9aa1a6;
  }
  * { box-sizing: border-box; margin: 0; padding: 0; }
  html, body {
    width: 1200px; height: 780px; overflow: hidden;
    background: var(--page-bg);
    font-family: "Open Sans", Arial, sans-serif;
  }
  .canvas {
    position: relative; width: 1200px; height: 780px;
    display: flex; align-items: center; justify-content: center; gap: 50px;
  }
  .card {
    width: 540px; height: 310px; position: relative;
    box-shadow: 0 6px 18px rgba(0,0,0,.18);
  }
  .card--front { background: var(--card-light); }
  .card--back { background: var(--card-dark); }

  .brand-block {
    position: absolute; left: 50px; top: 0; bottom: 0; width: 200px;
    display: flex; align-items: center; gap: 10px;
  }
  .brand-mark {
    width: 14px; height: 14px; background: var(--ink);
  }
  .brand-name {
    font-weight: 700; font-size: 40px; letter-spacing: 2px; color: var(--ink);
  }
  .divider {
    position: absolute; left: 268px; top: 50px; width: 1px; height: 210px;
    background: linear-gradient(to bottom, transparent, var(--divider) 30%, var(--divider) 70%, transparent);
  }
  .contact {
    position: absolute; left: 290px; top: 58px; right: 20px;
    color: var(--ink-soft);
  }
  .contact__name { font-weight: 700; font-size: 22px; color: var(--ink); line-height: 1.1; }
  .contact__role { font-size: 13px; margin-bottom: 12px; }
  .contact__address { font-size: 13.5px; line-height: 1.4; margin-bottom: 10px; }
  .contact__list { list-style: none; font-size: 13.5px; line-height: 1.55; }
  .contact__list li { display: flex; align-items: center; gap: 7px; }
  .contact__list svg { width: 12px; height: 12px; flex: none; fill: var(--ink); }
  .contact__list .no-icon { padding-left: 19px; }

  .back-brand {
    position: absolute; inset: 0; display: flex; align-items: center; justify-content: center; gap: 16px;
  }
  .back-brand .brand-mark { width: 20px; height: 20px; background: var(--emboss); }
  .back-brand .brand-name { font-size: 64px; color: var(--emboss); }
</style>
</head>
<body>
<main class="canvas">
  <section class="card card--front" aria-label="Business card front">
    <div class="brand-block">
      <span class="brand-mark"></span>
      <span class="brand-name">VOMRA</span>
    </div>
    <div class="divider"></div>
    <div class="contact">
      <p class="contact__name">Jordan Hale</p>
      <p class="contact__role">Co-Founder</p>
      <p class="contact__address">14-16 Marlow Lane Redfern<br>NSW 2016 Australia</p>
      <ul class="contact__list">
        <li><svg viewBox="0 0 24 24"><path d="M6.6 10.8a15.1 15.1 0 0 0 6.6 6.6l2.2-2.2a1 1 0 0 1 1-.25 11.4 11.4 0 0 0 3.6.57 1 1 0 0 1 1 1V20a1 1 0 0 1-1 1A17 17 0 0 1 3 4a1 1 0 0 1 1-1h3.5a1 1 0 0 1 1 1c0 1.25.2 2.45.57 3.57a1 1 0 0 1-.25 1z"/></svg>(555) 014-2276</li>
        <li><svg viewBox="0 0 24 24"><path d="M2 5h20v14H2zm2 2v.4l8 5 8-5V7zm0 2.8V17h16V9.8l-8 5z"/></svg>www.vomra.com.au</li>
        <li><svg viewBox="0 0 24 24"><path d="M12 2a10 10 0 1 0 0 20 10 10 0 0 0 0-20zm6.9 6h-3a15 15 0 0 0-1.3-4A8 8 0 0 1 18.9 8zM12 4c.8 1.1 1.5 2.5 1.9 4h-3.8c.4-1.5 1.1-2.9 1.9-4zM4.3 14a8 8 0 0 1 0-4h3.4a16 16 0 0 0 0 4zm.8 2h3a15 15 0 0 0 1.3 4A8 8 0 0 1 5.1 16zm3-8h-3a8 8 0 0 1 4.3-4 15 15 0 0 0-1.3 4zM12 20c-.8-1.1-1.5-2.5-1.9-4h3.8c-.4 1.5-1.1 2.9-1.9 4zm2.3-6H9.7a14 14 0 0 1 0-4h4.6a14 14 0 0 1 0 4zm.3 6a15 15 0 0 0 1.3-4h3a8 8 0 0 1-4.3 4zm1.7-6a16 16 0 0 0 0-4h3.4a8 8 0 0 1 0 4z"/></svg>admin@vomra.com.au</li>
      </ul>
    </div>
  </section>

  <section class="card card--back" aria-label="Business card back">
    <div class="back-brand">
      <span class="brand-mark"></span>
      <span class="brand-name">VOMRA</span>
    </div>
  </section>
</main>
</body>
</html>
```